BRELWINCare.co.uk - Mental Health Clinic for Child and Adolescents

Updated 29/01/2018***
I am not sure you guys are getting the idea regards to the opening page / homescreen layout. Can you look at the new images I have uploaded (page 5, 6 and 7) These are some of the layouts I like but to incorporate my chosen images, with the BRELWIN commissioner, buttons and a sliding header bar.
I have written a strong brief, I am looking for a website, preferably wordpress as i know they are easy to maintain. I am looking for a one page site, with the top / opening page being full screen image with drop down categories. I have made a rough design, see full brief in word doc attached, there is some freedom to play around with the design aspect but it will need to relay all the content provided. I like a minimal feel. I have also attached some images that may be useful, but will need a new logo for BRELWIN Care. I have attached some logo idea's, it is up to you decide whether you want to use them.
I would prefer the homepage as full screen image, and the categories offered as a drop down or over the main image.
I have also attached linked to some competitors websites:
https://www.vorimant-health.co.uk/
http://www.qlbn.org.uk/
Industry/Entity Type
Clinic
Number of Pages Required
1 page
Font styles to use
Look and feel
Each slider illustrates characteristics of the customer's brand and the style your logo design should communicate.

```html
<!DOCTYPE html>
<html lang="en">
<head>
<meta charset="utf-8">
<title>BRELWIN Care – Parents</title>
<link href="https://fonts.googleapis.com/css2?family=Open+Sans:wght@400;600;700&family=Ubuntu:wght@400;500;700&display=swap" rel="stylesheet">
<style>
:root{
  --white:#ffffff;
  --ink:#333333;
  --purple:#7a2f92;
  --magenta:#d61f8c;
  --pink:#e5007e;
  --green:#86c23f;
  --teal:#23b7d4;
  --orange:#ff641a;
  --blue:#1f8fde;
  --violet:#9b3fb0;
  --yellow:#ffe400;
  --menu:#1e2230;
}
*{box-sizing:border-box;margin:0;padding:0}
html,body{width:1200px;height:2596px;overflow:hidden}
body{font-family:"Open Sans",Arial,sans-serif;color:var(--ink);background:var(--white);position:relative}
h1,h2,h3{font-family:"Ubuntu","Open Sans",sans-serif;font-weight:500}

.site-header{height:132px;display:flex;align-items:center;justify-content:center;gap:14px}
.brand-mark{width:52px;height:52px;border-radius:50%;background:var(--orange)}
.brand-name{font-family:"Ubuntu",sans-serif;font-weight:700;font-size:34px;color:var(--purple)}

.main-nav{display:flex;height:68px;position:relative;z-index:5}
.main-nav a{flex:1;display:flex;align-items:center;justify-content:center;gap:8px;color:var(--white);text-decoration:none;font-size:14px;font-weight:600;text-transform:uppercase;letter-spacing:.5px;white-space:nowrap}
.main-nav a::before{content:"";width:14px;height:14px;border:2px solid rgba(255,255,255,.85);border-radius:3px}
.nav-about{background:var(--violet)}.nav-team{background:var(--magenta)}.nav-services{background:var(--green)}
.nav-contact{background:var(--teal)}.nav-parents{background:var(--purple)}.nav-commissioner{background:var(--pink)}
.nav-blog{background:var(--orange)}.nav-forum{background:var(--blue)}
.dropdown{position:absolute;left:300px;top:68px;width:180px;background:var(--menu);padding:10px 0;list-style:none}
.dropdown li{color:var(--white);font-size:14px;padding:8px 24px}
.dropdown li:first-child{color:var(--yellow)}

.hero{position:relative;height:460px;background:linear-gradient(135deg,#8a4aa0,#6a2a86 55%,#a064b4);display:flex;flex-direction:column;align-items:center;justify-content:center;color:var(--white)}
.hero-sun{width:70px;height:70px;margin-bottom:14px}
.hero h1{font-size:58px;letter-spacing:1px}

.promo-bar{position:relative;height:100px;background:var(--orange);display:flex;align-items:center;justify-content:space-between;padding:0 40px;color:var(--white)}
.promo-bar::before{content:"";position:absolute;left:50%;top:-18px;margin-left:-18px;border:18px solid transparent;border-top:0;border-bottom-color:var(--orange)}
.promo-bar p{font-family:"Ubuntu",sans-serif;font-size:32px;font-weight:500}
.promo-bar svg{width:28px;height:28px}

.about{height:520px;background:var(--purple);color:var(--white);text-align:center;padding-top:70px}
.section-title{font-size:42px;color:var(--white);display:inline-block;padding-bottom:12px;border-bottom:3px solid var(--white);margin-bottom:36px}
.about p{width:860px;margin:0 auto 22px;font-size:15px;line-height:1.7}
.btn{display:inline-block;background:var(--yellow);color:var(--ink);font-size:14px;font-weight:700;text-transform:uppercase;padding:12px 30px;border-radius:4px;text-decoration:none}

.blog{height:540px;background:var(--green);text-align:center;padding-top:50px}
.blog-grid{display:flex;justify-content:center;gap:40px;margin-top:4px}
.post{width:290px;color:var(--white)}
.post-image{position:relative;height:190px;border:4px solid var(--white)}
.post-date{position:absolute;left:0;top:10px;background:var(--orange);font-size:11px;padding:4px 10px}
.post h3{font-size:17px;margin:18px 0 10px;line-height:1.3}
.post p{font-size:12px;line-height:1.6}
.post small{display:block;margin-top:12px;font-size:12px}
.post small b{color:var(--purple)}

.contact{height:680px;background:linear-gradient(rgba(35,183,212,.92),rgba(35,183,212,.92)),linear-gradient(90deg,#6ec9dc,#2a8fb0);text-align:center;padding-top:50px;color:var(--white)}
.contact-body{display:flex;width:1040px;margin:60px auto 0;text-align:left}
.contact-form{display:grid;grid-template-columns:280px 280px;column-gap:36px;row-gap:34px;width:640px}
.field{border-bottom:2px solid var(--white);padding-bottom:28px;font-size:15px}
.field-message{grid-column:2;grid-row:1 / span 3}
.contact-form .btn{grid-column:1;width:120px;text-align:center;margin-top:4px}
.contact-info{list-style:none;border-left:1px solid rgba(255,255,255,.6);padding-left:40px;font-size:15px}
.contact-info li{display:flex;gap:16px;align-items:flex-start;margin-bottom:26px;line-height:1.5}
.contact-info svg{width:22px;height:22px;flex:none;margin-top:2px}

.site-footer{height:96px;display:flex;align-items:center;justify-content:center;font-size:14px;font-weight:600}
</style>
</head>
<body>

<header class="site-header">
  <span class="brand-mark"></span>
  <span class="brand-name">BRELWIN Care</span>
</header>

<nav class="main-nav">
  <a class="nav-about" href="#about">About</a>
  <a class="nav-team" href="#team">Our Team</a>
  <a class="nav-services" href="#services">Our Services</a>
  <a class="nav-contact" href="#contact">Contact Us</a>
  <a class="nav-parents" href="#parents">Parents</a>
  <a class="nav-commissioner" href="#commissioner">Commissioner</a>
  <a class="nav-blog" href="#blog">Blog</a>
  <a class="nav-forum" href="#forum">Forum</a>
  <ul class="dropdown">
    <li>ADHD</li><li>ASD</li><li>CBT</li><li>BRELWIN</li><li>Family Therapy</li>
  </ul>
</nav>

<section class="hero" role="img" aria-label="Photo of a parent and child at home with a purple colour overlay">
  <svg class="hero-sun" viewBox="0 0 70 70" aria-hidden="true">
    <circle cx="35" cy="35" r="13" fill="none" stroke="#ffe400" stroke-width="4"/>
    <g stroke="#ffe400" stroke-width="4" stroke-linecap="round">
      <line x1="35" y1="4" x2="35" y2="14"/><line x1="35" y1="56" x2="35" y2="66"/>
      <line x1="4" y1="35" x2="14" y2="35"/><line x1="56" y1="35" x2="66" y2="35"/>
      <line x1="13" y1="13" x2="20" y2="20"/><line x1="50" y1="50" x2="57" y2="57"/>
      <line x1="57" y1="13" x2="50" y2="20"/><line x1="20" y1="50" x2="13" y2="57"/>
    </g>
  </svg>
  <h1>PARENTS</h1>
</section>

<div class="promo-bar">
  <svg viewBox="0 0 28 28" aria-hidden="true"><path d="M18 4 L8 14 L18 24 M24 4 L14 14 L24 24" fill="none" stroke="#fff" stroke-width="3"/></svg>
  <p>ADHD and autism screening within 24 hours</p>
  <svg viewBox="0 0 28 28" aria-hidden="true"><path d="M10 4 L20 14 L10 24 M4 4 L14 14 L4 24" fill="none" stroke="#fff" stroke-width="3"/></svg>
</div>

<section class="about" id="about">
  <h2 class="section-title">ABOUT US</h2>
  <p>BRELWIN Care was formed with a vision to provide the very best child and adolescent assessments, therapy and aftercare. We have unique referral pathways that allow children and adolescents to be seen quickly by experienced clinicians who are highly skilled and some of the best in their chosen field.</p>
  <p>We have a renowned team of 25 clinicians for all ADHD and ASD screening, and aim to have you seen for a full ADHD or ASD assessment within 14 days. If your child has been diagnosed we offer follow-up care and ongoing post diagnostic support to both the child and family.</p>
  <a class="btn" href="#about">Read More</a>
</section>

<section class="blog" id="blog">
  <h2 class="section-title">BLOG</h2>
  <div class="blog-grid">
    <article class="post">
      <div class="post-image" role="img" aria-label="Photo of children playing outdoors in warm light" style="background:linear-gradient(135deg,#f3c27a,#b9854f)"><span class="post-date">Jan 20th 2018</span></div>
      <h3>Helping your child settle into a new school routine</h3>
      <p>Simple steps parents can take at home to ease worries, build confidence and keep mornings calm for the whole family.</p>
      <small>Posted by <b>BRELWIN</b></small>
    </article>
    <article class="post">
      <div class="post-image" role="img" aria-label="Photo of a child drawing at a table with a parent" style="background:linear-gradient(135deg,#e8d6c8,#c98a6a)"><span class="post-date">Jan 22nd 2018</span></div>
      <h3>Understanding the signs of ADHD in young children</h3>
      <p>What to look out for, when to ask for help and how an early assessment can make a real difference to your child.</p>
      <small>Posted by <b>BRELWIN</b></small>
    </article>
    <article class="post">
      <div class="post-image" role="img" aria-label="Photo of two young siblings smiling indoors" style="background:linear-gradient(135deg,#cfe3f0,#8fb8d6)"><span class="post-date">Jan 26th 2018</span></div>
      <h3>Family therapy and how it supports every member</h3>
      <p>How working together in sessions can improve communication, reduce stress and help families move forward together.</p>
      <small>Posted by <b>BRELWIN</b></small>
    </article>
  </div>
</section>

<section class="contact" id="contact">
  <h2 class="section-title">CONTACT US</h2>
  <div class="contact-body">
    <form class="contact-form">
      <div class="field">Name</div>
      <div class="field field-message">Message</div>
      <div class="field">E-Mail</div>
      <div class="field">Phone</div>
      <a class="btn" href="#contact">Send</a>
    </form>
    <ul class="contact-info">
      <li><svg viewBox="0 0 22 22" aria-hidden="true"><path d="M11 1a7 7 0 0 0-7 7c0 5 7 13 7 13s7-8 7-13a7 7 0 0 0-7-7z" fill="#fff"/><circle cx="11" cy="8" r="2.5" fill="#23b7d4"/></svg><span>Unit 7, 22 Harrowgate Lane,<br>Bristol, BS9 4XT</span></li>
      <li><svg viewBox="0 0 22 22" aria-hidden="true"><path d="M5 2l4 4-2 3c1 2 3 4 5 5l3-2 4 4-3 3C9 19 3 13 2 5z" fill="#fff"/></svg><span>0117 496 0321</span></li>
      <li><svg viewBox="0 0 22 22" aria-hidden="true"><circle cx="11" cy="11" r="9" fill="none" stroke="#fff" stroke-width="2"/><path d="M11 6v5l4 2" fill="none" stroke="#fff" stroke-width="2"/></svg><span>9am – 5pm Mon–Fri</span></li>
      <li><svg viewBox="0 0 22 22" aria-hidden="true"><rect x="2" y="5" width="18" height="12" fill="none" stroke="#fff" stroke-width="2"/><path d="M2 5l9 7 9-7" fill="none" stroke="#fff" stroke-width="2"/></svg><span>enquiry@brelwincare.co.uk</span></li>
    </ul>
  </div>
</section>

<footer class="site-footer">© 2018 Company Name | All Rights Reserved</footer>

</body>
</html>
```